Satchel & Sundial needs new business card design

I need a new business card design. I'm looking for out-of-the-box design which represents the freedom of being a location independent entrepreneur.
I offer coaching, retreats and trips.
I would like to see designs with and without the photo.
Colors I use are black (#000000), green (#25A796) and brown (#D7C38C)
Website satchelandsundial.example

Target Market(s)

location independent entrepreneurs, digital nomads, people looking to swap the 9 to 5 for a lifestyle business

Industry/Entity Type

Business

Contact Information for Business Card

Dorota Falkner
Your Lifestyle Business Coach, Retreat & Trip Leader
http://satchelandsundial.example
hello@satchelandsundial.example
Live a life you don't need a holiday from

Font styles to use
Serif
Sans Serif

Requirements
Must have
• One side should contain only the logo. I would also consider having the "Live a life you don't need a holiday from" on that side too (depending on how it looks)
• Please show both sides on the designs.

```html
<!DOCTYPE html>
<html lang="en">
<head>
<meta charset="utf-8">
<title>Satchel &amp; Sundial — Business Card</title>
<link rel="stylesheet" href="https://fonts.googleapis.com/css2?family=Source+Sans+3:ital,wght@0,400;0,600;0,700;1,700&display=swap">
<style>
  :root {
    --backdrop: #e9e4df;
    --card-dark: #231f20;
    --card-light: #ffffff;
    --brand-green: #25a796;
    --ink: #231f20;
    --text-light: #ffffff;
  }
  * { margin: 0; padding: 0; box-sizing: border-box; }
  html, body { width: 1200px; height: 900px; overflow: hidden; }
  body {
    background: var(--backdrop);
    font-family: "Source Sans 3", "Myriad Pro", Arial, sans-serif;
    position: relative;
  }
  .card {
    position: absolute;
    overflow: hidden;
    box-shadow: 0 6px 18px rgba(0,0,0,0.18);
  }
  /* Front side */
  .card-front {
    left: 77px; top: 34px;
    width: 589px; height: 364px;
    background: var(--card-dark);
  }
  .front-header {
    height: 156px;
    background: var(--card-light);
    padding: 44px 0 0 30px;
  }
  .wordmark {
    font-weight: 700;
    letter-spacing: 0.5px;
    line-height: 1;
  }
  .front-header .wordmark {
    color: var(--ink);
    font-size: 42px;
  }
  .front-body { padding: 16px 0 0 31px; }
  .person-name {
    color: var(--brand-green);
    font-weight: 700;
    font-size: 19px;
    line-height: 24px;
  }
  .person-role {
    color: var(--text-light);
    font-size: 15.5px;
    line-height: 22px;
    margin-left: 1px;
  }
  .contact-list {
    list-style: none;
    margin-top: 26px;
    color: var(--text-light);
    font-size: 15.5px;
    line-height: 22px;
  }
  .contact-list li { display: flex; align-items: center; gap: 7px; }
  .contact-icon { width: 11px; height: 11px; flex: none; }
  .tagline {
    margin-top: 19px;
    color: var(--text-light);
    font-weight: 700;
    font-style: italic;
    font-size: 18px;
  }
  /* Back side */
  .card-back {
    left: 388px; top: 505px;
    width: 567px; height: 352px;
    background: var(--card-dark);
  }
  .back-band {
    position: absolute;
    left: 0; top: 100px;
    width: 100%; height: 152px;
    background: var(--brand-green);
    display: flex; align-items: center; justify-content: center;
  }
  .back-band .wordmark {
    color: var(--text-light);
    font-size: 46px;
  }
</style>
</head>
<body>
  <section class="card card-front" aria-label="Business card front">
    <header class="front-header">
      <p class="wordmark">Satchel &amp; Sundial</p>
    </header>
    <div class="front-body">
      <h1 class="person-name">Dorota Falkner</h1>
      <p class="person-role">Your Lifestyle Business Coach Retreat &amp; Trip Leader</p>
      <ul class="contact-list">
        <li>
          <svg class="contact-icon" viewBox="0 0 12 12" aria-hidden="true">
            <rect x="0.5" y="2" width="11" height="8" fill="var(--brand-green)"/>
            <path d="M0.5 2 L6 6.5 L11.5 2" fill="none" stroke="var(--card-dark)" stroke-width="1"/>
          </svg>
          hello@satchelandsundial.example
        </li>
        <li>
          <svg class="contact-icon" viewBox="0 0 12 12" aria-hidden="true">
            <circle cx="6" cy="6" r="5.5" fill="var(--brand-green)"/>
            <path d="M0.5 6 H11.5 M6 0.5 C3 3 3 9 6 11.5 M6 0.5 C9 3 9 9 6 11.5" fill="none" stroke="var(--card-dark)" stroke-width="0.8"/>
          </svg>
          www.satchelandsundial.example
        </li>
      </ul>
      <p class="tagline">Live a life you don't need a holiday from</p>
    </div>
  </section>

  <section class="card card-back" aria-label="Business card back">
    <div class="back-band">
      <p class="wordmark">Satchel &amp; Sundial</p>
    </div>
  </section>
</body>
</html>
```